Architectural firm needs a graphic representation of our Master Planning process

We need an image to convey our 3-phase, 8-step Master Planning process that we utilize when designing plans for schools K-12. What we currently use looks very outdated in both the design and color scheme. We'd like an EPS created that can be scaled without distortion. The files I've attached show the current graphic and an instruction sheet which also contains our colors.

```html
<!DOCTYPE html>
<html lang="en">
<head>
<meta charset="utf-8">
<title>Master Planning Process</title>
<link rel="stylesheet" href="https://fonts.googleapis.com/css2?family=Montserrat:wght@400;500;700;800&display=swap">
<style>
  :root {
    --school: #1fc2c4;
    --school-light: #5fd6dc;
    --architect: #a50a33;
    --architect-band: #d4505f;
    --fund: #66d42a;
    --fund-band: #b4f21e;
    --ink: #666666;
    --node-grey: #bdbdbd;
    --line-grey: #aaaaaa;
    --dot-red: #d0103e;
    --purple: #7b6fd6;
    --yellow: #f9c80e;
    --bg: #ffffff;
  }
  html, body {
    margin: 0;
    padding: 0;
    overflow: hidden;
    background: var(--bg);
  }
  .canvas {
    width: 849px;
    height: 1200px;
    display: block;
  }
  .canvas text {
    font-family: "Montserrat", Arial, sans-serif;
  }
  .title { font-size: 40px; font-weight: 800; letter-spacing: 3px; text-anchor: middle; }
  .title--accent { fill: var(--architect); }
  .title--main { fill: var(--ink); }
  .party { font-size: 22px; font-weight: 700; letter-spacing: 2px; text-anchor: middle; }
  .party--school { fill: var(--school); }
  .party--architect { fill: var(--architect); }
  .party--fund { fill: var(--fund); }
  .step { font-size: 22px; font-weight: 800; letter-spacing: 2px; fill: var(--ink); }
  .step--left { text-anchor: end; }
  .step--wide { letter-spacing: 7px; }
  .legend-title { font-size: 22px; font-weight: 500; letter-spacing: 1px; fill: var(--ink); }
  .legend-item { font-size: 22px; font-weight: 500; letter-spacing: 1px; }
  .connector { stroke: var(--line-grey); stroke-width: 4; fill: none; }
  .node-step { fill: var(--node-grey); }
  .node-dot { fill: var(--dot-red); }
  .hub-ring { fill: #fff; stroke: var(--purple); stroke-width: 3; }
  .hub-core { fill: var(--purple); }
  .icon-purple { fill: var(--purple); }
  .icon-yellow { fill: var(--yellow); }
</style>
</head>
<body>
<svg class="canvas" viewBox="0 0 1050 1484" xmlns="http://www.w3.org/2000/svg">
  <defs>
    <g id="hub">
      <circle class="hub-ring" r="37"/>
      <circle class="hub-core" r="31"/>
      <circle cx="0" cy="-15" r="11" fill="#19e6f0"/>
      <circle cx="-13" cy="8" r="11" fill="#e8174a"/>
      <circle cx="14" cy="8" r="11" fill="#9fe84a"/>
    </g>
    <g id="step-node">
      <circle class="node-step" r="30"/>
      <circle class="node-dot" r="11"/>
    </g>
  </defs>

  <!-- Heading -->
  <text class="title title--accent" x="533" y="78">SPACE</text>
  <text class="title title--main" x="533" y="128">FOR TITLE</text>

  <!-- Parties -->
  <text class="party party--school" x="533" y="208">SCHOOL</text>
  <circle cx="530" cy="246" r="24" fill="var(--school)"/>

  <text class="party party--architect" x="334" y="282">ARCHITECTURAL</text>
  <text class="party party--architect" x="334" y="312">CONSULTANT</text>
  <circle cx="334" cy="354" r="24" fill="var(--architect)"/>

  <text class="party party--fund" x="727" y="282">FUNDRAISING</text>
  <text class="party party--fund" x="727" y="312">CONSULTANT</text>
  <circle cx="727" cy="354" r="24" fill="var(--fund)"/>

  <!-- Converging bands -->
  <g class="convergence">
    <path d="M520 288 L530 298 L540 288 L540 405 L520 405 Z" fill="var(--school-light)"/>
    <path d="M373 344 L500 344 Q525 344 525 369 L525 405 L505 405 L505 375 Q505 364 494 364 L373 364 L383 354 Z" fill="var(--architect-band)"/>
    <path d="M689 344 L560 344 Q535 344 535 369 L535 405 L555 405 L555 375 Q555 364 566 364 L689 364 L679 354 Z" fill="var(--fund-band)"/>
    <polygon points="487,400 565,400 526,440" fill="var(--architect-band)" opacity="0.55"/>
    <polygon points="495,400 575,400 534,440" fill="var(--fund-band)" opacity="0.6"/>
    <polygon points="505,410 555,410 530,452" fill="var(--school-light)" opacity="0.75"/>
  </g>

  <!-- Process connectors -->
  <path class="connector" d="M530 525 L476 621 L530 708 L584 621 Z"/>
  <line class="connector" x1="530" y1="708" x2="530" y2="1068"/>
  <polygon points="519,1066 541,1066 530,1090" fill="var(--line-grey)"/>

  <!-- Nodes -->
  <use href="#hub" x="530" y="525"/>
  <use href="#step-node" x="476" y="621"/>
  <use href="#step-node" x="584" y="621"/>
  <use href="#step-node" x="530" y="708"/>
  <use href="#step-node" x="530" y="795"/>
  <use href="#hub" x="530" y="890"/>
  <use href="#step-node" x="530" y="986"/>
  <use href="#hub" x="530" y="1132"/>

  <!-- Step icons -->
  <g role="img" aria-label="Eye with light bulb icon">
    <ellipse cx="674" cy="526" rx="38" ry="18" fill="none" stroke="var(--purple)" stroke-width="4"/>
    <circle cx="674" cy="524" r="11" class="icon-yellow"/>
  </g>
  <g role="img" aria-label="Building with magnifier icon">
    <rect x="396" y="577" width="33" height="74" class="icon-purple"/>
    <rect x="373" y="603" width="25" height="48" class="icon-purple"/>
    <circle cx="403" cy="650" r="12" fill="none" stroke="var(--yellow)" stroke-width="4"/>
    <line x1="411" y1="659" x2="420" y2="667" stroke="var(--yellow)" stroke-width="4"/>
  </g>
  <g role="img" aria-label="Puzzle pieces icon">
    <rect x="648" y="594" width="54" height="54" rx="6" class="icon-yellow"/>
    <rect x="648" y="594" width="27" height="27" rx="4" class="icon-purple"/>
    <rect x="675" y="621" width="27" height="27" rx="4" class="icon-purple"/>
  </g>
  <g role="img" aria-label="Alert speech bubble icon">
    <path d="M650 699 H700 V750 H686 L675 766 L664 750 H650 Z" class="icon-yellow" stroke="var(--purple)" stroke-width="3"/>
    <rect x="672" y="708" width="6" height="22" fill="var(--purple)"/>
    <circle cx="675" cy="738" r="3.5" fill="var(--purple)"/>
  </g>
  <g role="img" aria-label="Head with idea bulb icon">
    <path d="M378 795 Q372 760 402 755 Q432 756 432 790 Q432 805 424 812 L424 836 L392 836 L392 822 L378 816 Z" class="icon-purple"/>
    <circle cx="404" cy="787" r="13" class="icon-yellow"/>
  </g>
  <g role="img" aria-label="Checklist icon">
    <rect x="645" y="851" width="60" height="79" class="icon-purple"/>
    <path d="M655 868 l6 6 l10 -12 M655 891 l6 6 l10 -12" stroke="var(--yellow)" stroke-width="4" fill="none"/>
    <path d="M678 869 H698 M678 892 H698" stroke="#fff" stroke-width="3"/>
  </g>
  <g role="img" aria-label="Stacked documents icon">
    <rect x="370" y="948" width="44" height="58" class="icon-yellow" stroke="var(--purple)" stroke-width="3"/>
    <rect x="378" y="956" width="44" height="58" class="icon-yellow" stroke="var(--purple)" stroke-width="3"/>
    <path d="M386 965 H418 L432 979 V1023 H386 Z" class="icon-yellow" stroke="var(--purple)" stroke-width="3"/>
    <path d="M394 992 H424 M394 1002 H424 M394 1012 H424" stroke="var(--purple)" stroke-width="3"/>
  </g>
  <g role="img" aria-label="Rocket launch icon">
    <path d="M675 1080 Q690 1095 690 1120 L690 1146 L660 1146 L660 1120 Q660 1095 675 1080 Z" class="icon-purple"/>
    <circle cx="675" cy="1117" r="6" class="icon-yellow"/>
    <ellipse cx="675" cy="1168" rx="7" ry="15" class="icon-yellow"/>
  </g>

  <!-- Step labels -->
  <text class="step" x="730" y="535">VISIONING</text>
  <text class="step step--left" x="350" y="600">PHYSICAL</text>
  <text class="step step--left" x="350" y="630">CONDITIONS</text>
  <text class="step step--left" x="350" y="660">ASSESSMENT</text>
  <text class="step" x="730" y="600">SPACE</text>
  <text class="step step--wide" x="730" y="630">NEEDS</text>
  <text class="step" x="730" y="660">ASSESSMENT</text>
  <text class="step" x="727" y="729">PROBLEM DEFINED</text>
  <text class="step step--left" x="350" y="804">IDENTIFY SOLUTIONS</text>
  <text class="step" x="730" y="900">ASSESS &amp; SELECT</text>
  <text class="step step--left" x="350" y="995">COMPILE REPORT</text>
  <text class="step" x="727" y="1142">IMPLEMENT PLAN !</text>

  <!-- Legend -->
  <text class="legend-title" x="142" y="1285">Areas of responsibility colors meaning:</text>
  <circle cx="151" cy="1327" r="9" fill="var(--school)"/>
  <text class="legend-item" x="178" y="1335" fill="var(--school)">BLUE</text>
  <text class="legend-item" x="308" y="1335" fill="var(--school)">: SCHOOL</text>
  <circle cx="151" cy="1364" r="9" fill="var(--architect)"/>
  <text class="legend-item" x="178" y="1372" fill="var(--architect)">RED</text>
  <text class="legend-item" x="308" y="1372" fill="var(--architect)">: ARCHITECTURAL CONSULTANT</text>
  <circle cx="151" cy="1400" r="9" fill="var(--fund)"/>
  <text class="legend-item" x="178" y="1408" fill="var(--fund)">GREEN</text>
  <text class="legend-item" x="308" y="1408" fill="var(--fund)">: FUNDRAISING CONSULTANT</text>
</svg>
</body>
</html>
```